Consulting company business cards

We have a base design, but would be willing to update. We have a new logo/"tag" that needs to be added. Current business card design is attached for reference into our "style."

Industry/Entity Type

Business

Contact Information for Business Card

Should contain name and title, office number, mobile number if appropriate, e-mail, website, physical address, and company logo.

Font styles to use
Other font styles liked:
• See current card design on KorvandBCard

Colors
0455a3
85acd3
aaaaaa

Requirements
Must have
• Our colors are navy blue, gray, and a lighter blue
Nice to have
• Design that I can easily drop in new names/titles as we hire employees.

```html
<!DOCTYPE html>
<html lang="en">
<head>
<meta charset="utf-8">
<title>Skyloft Business Cards</title>
<link rel="stylesheet" href="https://fonts.googleapis.com/css2?family=Lato:wght@400;700;900&display=swap">
<style>
  :root {
    --navy: #0d3658;
    --light-blue: #6f9dc2;
    --gray: #8a8a8a;
    --text-dark: #2f3d4a;
    --card: #f7f8f9;
    --backdrop: #1c1c1c;
    --rule: #b9c2cb;
  }
  * { margin: 0; padding: 0; box-sizing: border-box; }
  html, body { width: 1200px; height: 873px; overflow: hidden; }
  body {
    background: var(--backdrop);
    font-family: "Lato", sans-serif;
    position: relative;
  }
  .card {
    position: absolute;
    width: 540px;
    height: 309px;
    background: var(--card);
    overflow: hidden;
  }
  .card--contact { left: 40px; top: 282px; }
  .card--brand { left: 620px; top: 282px; }

  .wordmark__name {
    font-weight: 900;
    color: var(--navy);
    letter-spacing: 1px;
    line-height: 1;
    white-space: nowrap;
  }
  .tagline {
    color: var(--gray);
    text-transform: uppercase;
    letter-spacing: 2px;
    font-weight: 400;
    white-space: nowrap;
  }

  /* Contact card */
  .card--contact .brand-block { position: absolute; left: 58px; top: 50px; }
  .card--contact .wordmark__name { font-size: 44px; }
  .card--contact .tagline { font-size: 10px; margin-top: 6px; }
  .divider {
    position: absolute; left: 292px; top: 48px;
    width: 1px; height: 84px; background: var(--rule);
  }
  .contact-list {
    position: absolute; left: 312px; top: 54px;
    list-style: none; font-size: 13px; color: var(--text-dark);
  }
  .contact-list li { display: flex; align-items: center; gap: 8px; height: 24px; white-space: nowrap; }
  .contact-list svg { width: 13px; height: 13px; fill: var(--text-dark); flex: none; }
  .person { position: absolute; left: 150px; top: 164px; text-align: right; }
  .person__name { font-size: 19px; color: var(--light-blue); font-weight: 400; }
  .person__name strong { color: var(--navy); font-weight: 700; }
  .person__title { font-size: 10px; color: var(--text-dark); font-weight: 700; }
  .address {
    position: absolute; left: 0; right: 0; top: 236px;
    text-align: center; font-size: 13px; font-weight: 700; color: var(--navy);
  }

  /* Brand card */
  .card--brand .brand-block { position: absolute; left: 48px; top: 62px; }
  .card--brand .wordmark__name { font-size: 86px; }
  .card--brand .tagline { font-size: 19px; margin-top: 8px; letter-spacing: 3px; }
  .website {
    position: absolute; left: 0; right: 0; top: 232px;
    text-align: center; font-size: 14px; letter-spacing: 5px;
    color: var(--text-dark); font-weight: 700;
  }

  .band { position: absolute; left: 0; bottom: 0; width: 540px; height: 40px; }
  .band__base { fill: var(--light-blue); }
  .band__tab { fill: var(--navy); }
</style>
</head>
<body>

<section class="card card--contact" aria-label="Contact side">
  <div class="brand-block">
    <p class="wordmark__name">SKYLOFT</p>
    <p class="tagline">Cloud Advisory Partners</p>
  </div>
  <div class="divider"></div>
  <ul class="contact-list">
    <li>
      <svg viewBox="0 0 16 16" aria-hidden="true"><path d="M3 1h3l1 4-2 1c1 2 3 4 5 5l1-2 4 1v3c0 1-1 2-2 2C7 15 1 9 1 3c0-1 1-2 2-2z"/></svg>
      555.018.4436
    </li>
    <li>
      <svg viewBox="0 0 16 16" aria-hidden="true"><path d="M4 1h8v4H4zM1 6h14v7h-3v2H4v-2H1zM5 10v4h6v-4z"/></svg>
      555.018.4470
    </li>
    <li>
      <svg viewBox="0 0 16 16" aria-hidden="true"><path d="M1 3h14v10H1zM2 4l6 5 6-5v-.2H2z"/></svg>
      Dkorvand@Skyloftgroup.com
    </li>
  </ul>
  <div class="person">
    <p class="person__name">Dana <strong>Korvand</strong></p>
    <p class="person__title">Office Manager</p>
  </div>
  <p class="address">1180 W 48th St Brookfield Ohio 40712</p>
  <svg class="band" viewBox="0 0 540 40" aria-hidden="true">
    <path class="band__base" d="M0 30 H296 C310 30 310 16 326 16 H540 V40 H0 Z"/>
    <path class="band__tab" d="M312 30 C322 30 322 20 336 20 H540 V30 Z"/>
  </svg>
</section>

<section class="card card--brand" aria-label="Brand side">
  <div class="brand-block">
    <p class="wordmark__name">SKYLOFT</p>
    <p class="tagline">Cloud Advisory Partners</p>
  </div>
  <p class="website">www.Skyloftgroup.com</p>
  <svg class="band" viewBox="0 0 540 40" aria-hidden="true">
    <path class="band__base" d="M0 30 H296 C310 30 310 16 326 16 H540 V40 H0 Z"/>
    <path class="band__tab" d="M312 30 C322 30 322 20 336 20 H540 V30 Z"/>
  </svg>
</section>

</body>
</html>
```